MRT Property - Business Cards

Looking for a business card & general letterhead, signage etc design for our new logo.

Colours:
000a20
0056a2
00b5ef
0088ce
68cef2

Fonts:
Poppins
Karla

Please keep look and feel of new brand - example in the zip package I sent.

```html
<!DOCTYPE html>
<html lang="en">
<head>
<meta charset="utf-8">
<title>MRT Property – Business Cards</title>
<link rel="stylesheet" href="https://fonts.googleapis.com/css2?family=Poppins:wght@300;400;500;600;700&display=swap">
<style>
  :root {
    --ink: #000a20;
    --brand-blue: #0056a2;
    --brand-cyan: #00b5ef;
    --brand-mid: #0088ce;
    --brand-sky: #68cef2;
    --band-light: #5ec0e4;
    --paper: #eceaea;
    --backdrop: #222222;
    --back-deep: #0b4a94;
  }
  * { box-sizing: border-box; margin: 0; padding: 0; }
  html, body { width: 1200px; height: 780px; overflow: hidden; }
  body {
    background: var(--backdrop);
    font-family: "Poppins", sans-serif;
    color: var(--ink);
  }
  .canvas {
    position: relative;
    width: 1200px;
    height: 780px;
    display: flex;
    align-items: center;
    justify-content: center;
    gap: 40px;
  }
  .card {
    position: relative;
    width: 540px;
    height: 310px;
    border-radius: 18px;
    overflow: hidden;
  }

  /* Front */
  .card--front { background: var(--paper); }
  .brand-name {
    position: absolute;
    left: 34px;
    top: 78px;
    display: flex;
    align-items: center;
    gap: 10px;
    font-weight: 700;
    font-size: 28px;
    color: var(--brand-blue);
    letter-spacing: 0.2px;
  }
  .brand-name__dot {
    width: 18px; height: 18px;
    border-radius: 50%;
    background: var(--brand-cyan);
  }
  .divider {
    position: absolute;
    left: 262px;
    top: 52px;
  }
  .person {
    position: absolute;
    left: 300px;
    top: 70px;
  }
  .person__name {
    font-size: 25px;
    line-height: 1.1;
    color: var(--brand-blue);
    font-weight: 700;
  }
  .person__surname { font-weight: 300; color: var(--brand-cyan); }
  .person__role {
    font-size: 12px;
    font-weight: 600;
    color: var(--ink);
    margin-top: 2px;
  }
  .contacts {
    position: absolute;
    left: 300px;
    top: 140px;
    list-style: none;
  }
  .contacts__item {
    display: flex;
    align-items: center;
    gap: 8px;
    font-size: 12.5px;
    font-weight: 500;
    line-height: 22px;
  }
  .contacts__icon { width: 13px; height: 13px; flex: none; }
  .address {
    position: absolute;
    left: 30px;
    bottom: 40px;
    font-size: 11.5px;
    font-weight: 500;
  }
  .band {
    position: absolute;
    left: 0; right: 0; bottom: 0;
    height: 30px;
    background: var(--band-light);
  }
  .band__accent {
    position: absolute;
    top: 0; bottom: 0; right: 0;
    width: 370px;
    background: var(--brand-blue);
    clip-path: polygon(12px 0, 100% 0, 100% 100%, 0 100%);
  }

  /* Back */
  .card--back {
    background: radial-gradient(ellipse at 88% 35%, var(--brand-mid) 0%, var(--back-deep) 55%, #0a3f86 100%);
  }
  .back-pattern { position: absolute; inset: 0; }
  .back-brand {
    position: absolute;
    right: 70px;
    bottom: 70px;
    font-weight: 700;
    font-size: 15px;
    color: #ffffff;
  }
</style>
</head>
<body>
<main class="canvas">

  <section class="card card--front" aria-label="Business card front">
    <div class="brand-name"><span class="brand-name__dot"></span>MRT Property</div>

    <svg class="divider" width="30" height="150" viewBox="0 0 30 150" aria-hidden="true">
      <line x1="28" y1="0" x2="2" y2="150" stroke="var(--brand-blue)" stroke-width="1"/>
    </svg>

    <div class="person">
      <p class="person__name">Callum <span class="person__surname">Reeve</span></p>
      <p class="person__role">Director</p>
    </div>

    <ul class="contacts">
      <li class="contacts__item">
        <svg class="contacts__icon" viewBox="0 0 24 24" aria-hidden="true"><path fill="var(--brand-mid)" d="M6.6 10.8a15.1 15.1 0 0 0 6.6 6.6l2.2-2.2c.3-.3.7-.4 1-.2 1.1.4 2.3.6 3.6.6.6 0 1 .4 1 1V20c0 .6-.4 1-1 1A17 17 0 0 1 3 4c0-.6.4-1 1-1h3.5c.6 0 1 .4 1 1 0 1.3.2 2.5.6 3.6.1.3 0 .7-.2 1z"/></svg>
        +61 2 9555 0142
      </li>
      <li class="contacts__item">
        <svg class="contacts__icon" viewBox="0 0 24 24" aria-hidden="true"><circle cx="12" cy="12" r="10" fill="var(--brand-mid)"/><path d="M2 12h20M12 2c3 3 3 17 0 20M12 2c-3 3-3 17 0 20" stroke="#fff" stroke-width="1.4" fill="none"/></svg>
        www.mrtproperty.com.au
      </li>
      <li class="contacts__item">
        <svg class="contacts__icon" viewBox="0 0 24 24" aria-hidden="true"><rect x="2" y="5" width="20" height="14" rx="2" fill="var(--brand-mid)"/><path d="M3 6l9 7 9-7" stroke="#fff" stroke-width="1.6" fill="none"/></svg>
        info@mrtproperty.com.au
      </li>
    </ul>

    <p class="address">Suite 3.04, Level 3, 18 Harbourline Way, Rhodes Point NSW 2138</p>

    <div class="band"><div class="band__accent"></div></div>
  </section>

  <section class="card card--back" aria-label="Business card back">
    <div class="back-pattern" role="img" aria-label="Repeating brand pattern in deep and light blue tones"></div>
    <div class="back-brand">MRT Property</div>
  </section>

</main>
</body>
</html>
```